Self-Publisher seeking a professional Book Cover design

Paperback novel, science-fiction/mind-fiction. Title “Tolvar’s Hollow”. Will be published via Brindle PressLine and must meet their sizing requirements for a Book Cover (‘the spine”). (The book is 362 pages). The overall concept of design should be relatively simple, playing with themes of dark/blackness/space/unconscious/insanity-themes. Initially I had in mind a dark cover with something floating small and distant in the darkness like a sort of “space-cocoon”/hibernation-tank for an astronaut. (just something to get started thinking with). I am very open to any concepts.

From the back cover:
“In the year 3438, a discovery of a lifetime is made, and promises new light for a whole new generation of mankind which has permanently stagnated, becoming little more than slaves to their own technology which itself has already plateaued. Life goes on, yet for man, it stopped over a millennia ago. A secret project begun in the Ancient-American West in the year 1947, has catastrophic implications for the modern people’s of 3438. A discovery in space that lay apparently dormant for over a thousand years, mysteriously hidden from mankind’s ever evolving technological grasp, leads to a culture-shattering revelation that can only have one outcome. Chaos. …”

Target Market(s)

25-45 yr.

Industry/Entity Type

science-fiction, mind-bending, esotericism, psychological, space,

Font styles to use
Serif

Colors

Designer to choose colors to be used in the design.

Requirements
Must have
• darkness, with perhaps elements of bright light???
Should not have
• nothing too colorful. think, “unconscious”.

```html
<!DOCTYPE html>
<html lang="en">
<head>
<meta charset="UTF-8">
<title>Tolvar’s Hollow — Paperback Cover</title>
<link rel="stylesheet" href="https://fonts.googleapis.com/css2?family=Russo+One&family=Pathway+Gothic+One&family=Syncopate&display=swap">
<style>
  :root {
    --space-black: #0b080d;
    --space-deep: #120c16;
    --title-white: #f2f2f2;
    --title-yellow: #f5c300;
    --body-white: #f4f4f4;
    --glow-core: #ffe6ff;
    --glow-pink: #d23cc8;
    --lunar-light: #c9ccd4;
    --lunar-shadow: #2a2d35;
    --barcode-white: #ffffff;
  }
  * { margin: 0; padding: 0; box-sizing: border-box; }
  html, body { width: 1200px; height: 900px; overflow: hidden; background: var(--space-black); }
  .cover-wrap {
    position: relative;
    width: 1200px; height: 900px;
    background:
      radial-gradient(ellipse 60% 70% at 25% 45%, var(--space-deep), transparent 70%),
      radial-gradient(ellipse 60% 70% at 77% 45%, var(--space-deep), transparent 70%),
      var(--space-black);
    overflow: hidden;
  }
  .star-glow {
    position: absolute;
    width: 60px; height: 60px;
    border-radius: 50%;
    background: radial-gradient(circle, var(--glow-core) 0%, var(--glow-pink) 28%, rgba(210,60,200,0.25) 50%, transparent 72%);
  }
  .star-glow--back { left: 70px; top: 51px; }
  .star-glow--front { left: 697px; top: 78px; }

  .title-block { position: absolute; }
  .title-block svg { display: block; overflow: visible; }
  .title-line { font-family: "Russo One", sans-serif; }
  .title-line--top { fill: var(--title-white); }
  .title-line--bottom { fill: var(--title-yellow); }
  .title-block--back { left: 152px; top: 132px; }
  .title-block--front { left: 671px; top: 168px; }

  .blurb {
    position: absolute;
    left: 187px; top: 282px;
    width: 326px;
    font-family: "Pathway Gothic One", sans-serif;
    font-size: 22.4px;
    line-height: 26.6px;
    color: var(--body-white);
    text-align: justify;
    text-align-last: left;
  }
  .barcode-space {
    position: absolute;
    left: 308px; top: 713px;
    width: 199px; height: 120px;
    background: var(--barcode-white);
  }

  .spine { position: absolute; left: 586px; top: 0; width: 30px; height: 900px; }
  .spine svg { display: block; }
  .spine-title { font-family: "Russo One", sans-serif; font-size: 31px; }
  .spine-title .word-top { fill: var(--title-white); }
  .spine-title .word-bottom { fill: var(--title-yellow); }
  .spine-author { font-family: "Syncopate", sans-serif; font-size: 22px; fill: var(--title-white); }

  .lunar-scene {
    position: absolute;
    left: 700px; top: 515px;
    width: 280px; height: 170px;
    border-radius: 50%;
    background:
      radial-gradient(ellipse 30% 22% at 56% 28%, rgba(255,235,255,0.9), transparent 70%),
      radial-gradient(ellipse 50% 50% at 50% 50%, var(--lunar-light) 0%, var(--lunar-shadow) 60%, transparent 100%);
    opacity: 0.85;
  }

  .author-name {
    position: absolute;
    left: 716px; top: 812px;
    font-family: "Syncopate", sans-serif;
    font-size: 22px;
    letter-spacing: 17px;
    color: var(--title-white);
    white-space: nowrap;
    line-height: 1;
  }
</style>
</head>
<body>
<main class="cover-wrap">

  <section class="back-cover">
    <div class="star-glow star-glow--back"></div>
    <div class="title-block title-block--back">
      <svg width="352" height="110" viewBox="0 0 352 110" aria-label="Tolvar’s Hollow">
        <text class="title-line title-line--top" x="0" y="46" font-size="50" textLength="351" lengthAdjust="spacingAndGlyphs">TOLVAR’S</text>
        <text class="title-line title-line--bottom" x="0" y="107" font-size="62" textLength="351" lengthAdjust="spacingAndGlyphs">HOLLOW</text>
      </svg>
    </div>
    <p class="blurb">“In the year 3438, a discovery of a lifetime is made, and promises new light for a whole new generation of mankind which has permanently stagnated, becoming little more than slaves to their own technology which itself has already plateaued. Life goes on, yet for man, it stopped over a millennia ago. A secret project begun in the Ancient-American West in the year 1947, has catastrophic implications for the modern people’s of 3438. A discovery in space that lay apparently dormant for over a thousand years, mysteriously hidden from mankind’s ever evolving technological grasp, leads to a culture-shattering revelation that can only have one outcome. Chaos. …”</p>
    <div class="barcode-space"></div>
  </section>

  <section class="spine">
    <svg width="30" height="900" viewBox="0 0 30 900">
      <text class="spine-title" transform="translate(3,52) rotate(90)" textLength="376" lengthAdjust="spacingAndGlyphs"><tspan class="word-top">TOLVAR’S </tspan><tspan class="word-bottom">HOLLOW</tspan></text>
      <text class="spine-author" transform="translate(7,575) rotate(90)" textLength="258" lengthAdjust="spacing">AUTHOR NAME</text>
    </svg>
  </section>

  <section class="front-cover">
    <div class="star-glow star-glow--front"></div>
    <div class="title-block title-block--front">
      <svg width="482" height="150" viewBox="0 0 482 150" aria-label="Tolvar’s Hollow">
        <text class="title-line title-line--top" x="0" y="62" font-size="66" textLength="480" lengthAdjust="spacingAndGlyphs">TOLVAR’S</text>
        <text class="title-line title-line--bottom" x="0" y="147" font-size="88" textLength="482" lengthAdjust="spacingAndGlyphs">HOLLOW</text>
      </svg>
    </div>
    <div class="lunar-scene" role="img" aria-label="A lone astronaut drifting above a glowing cratered moon surface in dark space"></div>
    <div class="author-name">AUTHOR NAME</div>
  </section>

</main>
</body>
</html>
```